Create modern and sleek business card for luxury real estate company

We're a "boutique" real estate office looking for a design that gets across a highly modern luxury brand. Blacks and whites are probably the best colors unless we try a silver foil for the logo. I've attached a version of our current logo here. I'd like to swap out the current font on there with Gotham Light Regular.

I'm looking to have one side of the card have the logo with the space for our agents info on the other side.

Target Market(s)

Young professionals in a "luxury" headspace

Industry/Entity Type

Real estate

Contact Information for Business Card

A place for agent name, cell number, website. The slogan "Quietly Redefining Fine Homes".

Font styles to use
Other font styles liked:
• Gotham Regular

Colors

Designer to choose only greyscale colors for use in the design.

Requirements
Must have
• Matte black as the background color. Clean lines and use of contrast. A specific design aspect that will use silver foil.
Nice to have
• Up in the air on integrating a QR code
Should not have
• Any houses or other real estate related design (ex: a clip art house)

```html
<!DOCTYPE html>
<html lang="en">
<head>
<meta charset="utf-8">
<title>Halden Estates – Business Card</title>
<link href="https://fonts.googleapis.com/css2?family=Open+Sans:wght@400;700&display=swap" rel="stylesheet">
<style>
  :root {
    --backdrop: #3b3b3b;
    --card-black: #0e0e0e;
    --ink-white: #f2f2f2;
    --ink-grey: #7a7a7a;
    --foil-silver: #c9c9c9;
    --rule: #8c8c8c;
  }
  * { margin: 0; padding: 0; box-sizing: border-box; }
  html, body {
    width: 1200px; height: 801px; overflow: hidden;
    background: var(--backdrop);
    font-family: "Open Sans", Arial, sans-serif;
  }
  .stage {
    width: 1200px; height: 801px;
    display: flex; align-items: center; justify-content: center; gap: 48px;
  }
  .card {
    width: 525px; height: 300px;
    background: var(--card-black);
    position: relative;
    box-shadow: 0 10px 28px rgba(0,0,0,.45);
  }
  /* Info side */
  .card-info .brand {
    position: absolute; left: 34px; top: 96px;
    display: flex; align-items: center; gap: 14px;
  }
  .brand-dot {
    width: 46px; height: 46px; border-radius: 50%;
    border: 2px solid var(--ink-white);
    flex: none;
  }
  .brand-name {
    color: var(--ink-white); font-weight: 400;
    font-size: 21px; letter-spacing: 2px; line-height: 1.15;
    text-transform: uppercase;
  }
  .divider {
    position: absolute; left: 268px; top: 58px;
    width: 1px; height: 150px; background: var(--rule);
  }
  .agent {
    position: absolute; left: 290px; top: 60px; color: var(--ink-white);
  }
  .agent-name { font-weight: 700; font-size: 19px; letter-spacing: .5px; }
  .agent-title { color: var(--ink-grey); font-size: 14px; margin-bottom: 12px; }
  .contact { list-style: none; font-size: 13.5px; }
  .contact li { display: flex; align-items: center; gap: 8px; line-height: 22px; }
  .contact svg { width: 11px; height: 11px; fill: var(--ink-white); flex: none; }
  .slogan {
    position: absolute; left: 0; right: 0; bottom: 28px;
    text-align: center; color: var(--ink-white); font-size: 13.5px;
  }
  /* Logo side */
  .card-logo {
    display: flex; align-items: center; justify-content: center; gap: 22px;
  }
  .card-logo .brand-dot {
    width: 92px; height: 92px; border: 3px solid #2a2a2a;
  }
  .card-logo .brand-name {
    color: var(--foil-silver); font-size: 38px; letter-spacing: 3px; line-height: 1.1;
  }
</style>
</head>
<body>
<main class="stage">
  <section class="card card-info">
    <div class="brand">
      <span class="brand-dot"></span>
      <span class="brand-name">Halden<br>Estates</span>
    </div>
    <span class="divider"></span>
    <div class="agent">
      <p class="agent-name">DANIEL ARVEY</p>
      <p class="agent-title">President</p>
      <ul class="contact">
        <li><svg viewBox="0 0 24 24"><path d="M6.6 10.8a15 15 0 0 0 6.6 6.6l2.2-2.2c.3-.3.7-.4 1-.2 1.1.4 2.3.6 3.6.6.6 0 1 .4 1 1V20c0 .6-.4 1-1 1A17 17 0 0 1 3 4c0-.6.4-1 1-1h3.5c.6 0 1 .4 1 1 0 1.3.2 2.5.6 3.6.1.3 0 .7-.2 1z"/></svg>555-010-4821</li>
        <li><svg viewBox="0 0 24 24"><path d="M2 5h20v14H2zm2 2v.5l8 5 8-5V7z"/></svg>darvey@haldenestates.com</li>
        <li><svg viewBox="0 0 24 24"><circle cx="12" cy="12" r="10"/></svg>www.haldenestates.com</li>
      </ul>
    </div>
    <p class="slogan">Quietly Redefining Fine Homes</p>
  </section>

  <section class="card card-logo">
    <span class="brand-dot"></span>
    <span class="brand-name">Halden<br>Estates</span>
  </section>
</main>
</body>
</html>
```